New Business Card Design Project

We require a business card design for Vexalund, a newly established Indian company.
Our focus is on the development, manufacturing, and export of a diverse array of pharmaceutical products on a global scale. The card should convey a professional appearance, as our primary markets are in Africa, China, and Southeast Asian nations.
We envision a two-sided business card, with the reverse side dedicated to a logo set against a solid color or an elegantly designed pattern. The corners should be rounded. We would appreciate seeing both horizontal and vertical design options. We trust the designer to utilize their expertise in creating this design.

The content for the business card is included in the attached Word file.

Target Market(s)

Our primary markets are in Africa, China, and Southeast Asian, Latin America, Maldives, Sri Lanka

Industry/Entity Type

Pharmaceutical Manufacturing and Export

Contact Information for Business Card

Colors

Designer to choose colors to be used in the design.

Requirements
Must have
• The reverse side of the business card features solely the logo along with the tagline, "Care for Tomorrow."
Should not have
• The logo should not exceed two instances, encompassing both the front and back sides of the card.

```html
<!DOCTYPE html>
<html lang="en">
<head>
<meta charset="utf-8">
<title>Vexalund Business Card</title>
<link href="https://fonts.googleapis.com/css2?family=Poppins:wght@400;600&family=Open+Sans:wght@400;700&display=swap" rel="stylesheet">
<style>
  :root {
    --stage: #232323;
    --card-blue: #2ea8e0;
    --coral: #f06552;
    --white: #ffffff;
  }
  * { margin: 0; padding: 0; box-sizing: border-box; }
  html, body {
    width: 1200px; height: 711px; overflow: hidden;
    background: var(--stage);
  }
  .canvas { position: relative; width: 1200px; height: 711px; }
  .card {
    position: absolute; top: 207px; width: 519px; height: 296px;
    border-radius: 19px; background: var(--card-blue);
    overflow: hidden; color: var(--white);
    box-shadow: 0 6px 16px rgba(0,0,0,0.55);
  }
  .card--front { left: 77px; }
  .card--back { left: 604px; }

  .brand-name {
    font-family: "Poppins", sans-serif;
    font-weight: 600; font-size: 35px; line-height: 1; letter-spacing: -0.3px;
  }
  .card--front .brand-name { position: absolute; left: 18px; top: 100px; }
  .brand-dot {
    position: absolute; width: 16px; height: 16px; border-radius: 50%;
    background: var(--white);
  }
  .card--front .brand-dot { left: 20px; top: 70px; }

  .accent-bar {
    position: absolute; left: 0; top: 153px; width: 11px; height: 37px;
    background: var(--white);
  }
  .person-name {
    position: absolute; left: 18px; top: 150px;
    font-family: "Open Sans", sans-serif; font-size: 21px; line-height: 1.2;
    font-weight: 400;
  }
  .person-name strong { font-weight: 700; }
  .person-role {
    position: absolute; left: 18px; top: 175px;
    font-family: "Open Sans", sans-serif; font-size: 11.5px;
  }
  .address {
    position: absolute; left: 18px; top: 197px;
    font-family: "Open Sans", sans-serif; font-size: 11px; line-height: 14.5px;
  }
  .contact-list {
    position: absolute; left: 18px; top: 236px; list-style: none;
    font-family: "Open Sans", sans-serif; font-size: 11px; line-height: 14.6px;
  }
  .contact-list li { display: flex; align-items: center; gap: 6px; }
  .contact-list svg { width: 10px; height: 10px; flex: none; }

  .decor-panel {
    position: absolute; top: 0; height: 296px; width: 173px;
  }
  .card--front .decor-panel {
    right: 0;
    background: linear-gradient(160deg, var(--white) 0%, var(--white) 20%, #bfe4f5 45%, var(--card-blue) 100%);
  }
  .card--back .decor-panel {
    left: 0;
    background: linear-gradient(200deg, var(--white) 0%, var(--white) 20%, #f8c4bb 45%, var(--coral) 100%);
  }

  .back-lockup {
    position: absolute; right: 19px; top: 226px;
    text-align: center;
  }
  .card--back .brand-dot { right: 75px; top: 195px; }
  .tagline {
    margin-top: 6px;
    font-family: "Poppins", sans-serif; font-size: 12.5px; font-weight: 400;
    line-height: 1.2;
  }
</style>
</head>
<body>
<main class="canvas">
  <section class="card card--front">
    <span class="brand-dot"></span>
    <div class="brand-name">Vexalund</div>
    <span class="accent-bar"></span>
    <div class="person-name"><strong>Ravin</strong> K. Tholar</div>
    <div class="person-role">CEO</div>
    <p class="address">14, Neelkamal Nagar,<br>Sorampur, 440217, India</p>
    <ul class="contact-list">
      <li>
        <svg viewBox="0 0 10 10"><rect x="2.2" y="0.6" width="5.6" height="8.8" rx="0.8" fill="none" stroke="#fff" stroke-width="1"/></svg>
        +91 98 7650 3214
      </li>
      <li>
        <svg viewBox="0 0 10 10"><circle cx="5" cy="5" r="4.3" fill="none" stroke="#fff" stroke-width="1"/><path d="M0.7 5h8.6M5 0.7c-2.4 2.6-2.4 6 0 8.6M5 0.7c2.4 2.6 2.4 6 0 8.6" fill="none" stroke="#fff" stroke-width="0.8"/></svg>
        www.vexalund.com
      </li>
      <li>
        <svg viewBox="0 0 10 10"><rect x="0.6" y="2" width="8.8" height="6.4" fill="none" stroke="#fff" stroke-width="1"/><path d="M0.6 2l4.4 3.6L9.4 2" fill="none" stroke="#fff" stroke-width="1"/></svg>
        rtholar@vexalund.com
      </li>
    </ul>
    <div class="decor-panel" role="img" aria-label="Large brand decoration in white and blue"></div>
  </section>

  <section class="card card--back">
    <div class="decor-panel" role="img" aria-label="Large brand decoration in white and coral"></div>
    <span class="brand-dot"></span>
    <div class="back-lockup">
      <div class="brand-name">Vexalund</div>
      <div class="tagline">Care for Tomorrow.</div>
    </div>
  </section>
</main>
</body>
</html>
```